New business card/stationary for a consulting company

I am looking for a clean and very professional looking business card for my consulting company as well as corresponding stationary. I am uploading our logo. I like simple and powerful for the feel. No graphics but I am open on everything else. Below is my contact information but would like the final to be in a version I can add my employees information into and print. Thank you.

Daniel Whitcombe
dan@ferncliffadvisory.com
2870 North 9th Avenue, Summit Floor, Elm Ridge, Illinois 60531
www.ferncliffadvisory.com

Industry/Entity Type

Consulting

Contact Information for Business Card

Daniel Whitcombe
dan@ferncliffadvisory.com
www.ferncliffadvisory.com

Font styles to use
Serif
Sans Serif

Requirements
Must have
• Our logo and the business card details.
Nice to have
• our website www.ferncliffadvisory.com

```html
<!DOCTYPE html>
<html lang="en">
<head>
<meta charset="utf-8">
<title>Ferncliff Advisory – Business Card</title>
<link href="https://fonts.googleapis.com/css2?family=Crimson+Text:wght@400;700&family=Montserrat:wght@400&display=swap" rel="stylesheet">
<style>
  :root {
    --navy: #06056b;
    --white: #ffffff;
    --ink: #1a1a1a;
    --rule: #d6d6d6;
    --backdrop: #e6eaea;
  }
  html, body {
    margin: 0;
    padding: 0;
    width: 1200px;
    height: 900px;
    overflow: hidden;
    background: var(--backdrop);
  }
  .canvas {
    position: relative;
    width: 1200px;
    height: 900px;
    display: flex;
    align-items: center;
    justify-content: center;
    gap: 60px;
  }
  .card {
    width: 520px;
    height: 300px;
    position: relative;
    box-shadow: 0 2px 6px rgba(0,0,0,0.12);
    box-sizing: border-box;
  }
  .card--front {
    background: var(--navy);
    display: flex;
    flex-direction: column;
    align-items: center;
    justify-content: center;
    gap: 22px;
  }
  .brand {
    display: flex;
    align-items: center;
    gap: 14px;
    font-family: "Montserrat", sans-serif;
    font-weight: 400;
    letter-spacing: 0.16em;
    text-transform: uppercase;
    white-space: nowrap;
  }
  .brand__mark {
    display: block;
    flex: none;
  }
  .card--front .brand {
    color: var(--white);
    font-size: 26px;
  }
  .card--front .brand__mark {
    width: 26px;
    height: 26px;
    background: var(--white);
  }
  .card--back {
    background: var(--white);
    padding: 48px 0 0 62px;
  }
  .card--back .brand {
    color: var(--navy);
    font-size: 19px;
  }
  .card--back .brand__mark {
    width: 20px;
    height: 20px;
    background: var(--navy);
  }
  .contact {
    margin-top: 30px;
    font-family: "Crimson Text", serif;
    color: var(--ink);
  }
  .contact__name {
    font-weight: 700;
    font-size: 21px;
    margin: 0;
    padding-bottom: 10px;
    border-bottom: 1px solid var(--rule);
    width: 190px;
  }
  .contact__address {
    font-size: 14px;
    line-height: 1.25;
    margin: 12px 0 12px;
    font-style: normal;
  }
  .contact__line {
    display: flex;
    align-items: center;
    gap: 7px;
    font-size: 14px;
    line-height: 1.3;
  }
  .contact__icon {
    width: 10px;
    height: 10px;
    flex: none;
  }
</style>
</head>
<body>
<main class="canvas">
  <section class="card card--front" aria-label="Card front">
    <div class="brand">
      <span class="brand__mark"></span>
      <span class="brand__name">Ferncliff Advisory</span>
    </div>
  </section>

  <section class="card card--back" aria-label="Card back">
    <div class="brand">
      <span class="brand__mark"></span>
      <span class="brand__name">Ferncliff Advisory</span>
    </div>
    <div class="contact">
      <p class="contact__name">Daniel Whitcombe</p>
      <address class="contact__address">
        2870 North 9th Avenue, Summit Floor<br>
        Elm Ridge, Illinois 60531
      </address>
      <div class="contact__line">
        <svg class="contact__icon" viewBox="0 0 10 10" aria-hidden="true">
          <rect x="0.5" y="2" width="9" height="6.5" fill="#1a1a1a"/>
          <polyline points="0.5,2 5,6 9.5,2" fill="none" stroke="#fff" stroke-width="0.9"/>
        </svg>
        <span>dan@ferncliffadvisory.com</span>
      </div>
      <div class="contact__line">
        <svg class="contact__icon" viewBox="0 0 10 10" aria-hidden="true">
          <circle cx="5" cy="5" r="4.3" fill="none" stroke="#1a1a1a" stroke-width="1"/>
          <ellipse cx="5" cy="5" rx="1.8" ry="4.3" fill="none" stroke="#1a1a1a" stroke-width="0.8"/>
          <line x1="0.7" y1="5" x2="9.3" y2="5" stroke="#1a1a1a" stroke-width="0.8"/>
        </svg>
        <span>www.ferncliffadvisory.com</span>
      </div>
    </div>
  </section>
</main>
</body>
</html>
```